Corporate Business Card

Very professional, Modern, Not to busy, include phone address email, website
(253) 617-4930, 18761 52nd Avenue S, Kent, WA 98047, martin@plumlinegroup.com, varkoworks.com

Target Market(s)

Manufacturing

Industry/Entity Type

Aero, machining, manufacturing, Off road racing

Contact Information for Business Card

Phone, address email, website

```html
<!DOCTYPE html>
<html lang="en">
<head>
<meta charset="utf-8">
<title>Varko Works — Business Card</title>
<link rel="stylesheet" href="https://fonts.googleapis.com/css2?family=Montserrat:wght@400;500;700&display=swap">
<style>
  :root {
    --navy: #16346e;
    --red: #d42027;
    --white: #ffffff;
    --ink: #1a1a1a;
    --backdrop: #c9c9cb;
  }
  * { margin: 0; padding: 0; box-sizing: border-box; }
  html, body { width: 1200px; height: 813px; overflow: hidden; }
  body {
    background: var(--backdrop);
    font-family: "Montserrat", sans-serif;
    position: relative;
  }
  .card {
    position: absolute;
    width: 540px;
    height: 309px;
    border-radius: 22px;
    overflow: hidden;
    box-shadow: 0 10px 28px rgba(0,0,0,0.28);
  }
  .card-front { left: 50px; top: 110px; background: var(--white); }
  .card-back { left: 610px; top: 394px; background: var(--navy); }

  .front-wave { position: absolute; inset: 0; width: 540px; height: 309px; }

  .brand { position: absolute; }
  .brand-name {
    font-weight: 700;
    letter-spacing: 0.5px;
    white-space: nowrap;
    line-height: 1;
  }
  .brand-rule { position: absolute; height: 2px; }

  .card-front .brand { left: 150px; top: 48px; }
  .card-front .brand-name { font-size: 40px; color: var(--navy); }
  .card-front .brand-rule { left: 0; top: 58px; width: 170px; background: var(--navy); }

  .card-back .brand { left: 100px; top: 106px; }
  .card-back .brand-name { font-size: 54px; color: var(--white); }
  .card-back .brand-rule { left: 0; top: 76px; width: 230px; background: var(--white); }

  .contact {
    position: absolute;
    left: 36px;
    top: 148px;
    color: var(--ink);
    font-size: 13.5px;
    font-weight: 500;
    line-height: 1.4;
  }
  .address { margin-bottom: 18px; }
  .contact-list { list-style: none; }
  .contact-list li {
    display: flex;
    align-items: center;
    gap: 8px;
    height: 22px;
  }
  .contact-icon { width: 13px; height: 13px; flex: none; }
</style>
</head>
<body>

  <section class="card card-front" aria-label="Business card front">
    <svg class="front-wave" viewBox="0 0 540 309" aria-hidden="true">
      <path d="M482,0 C452,130 382,200 302,245 C252,272 217,290 202,309 L540,309 L540,0 Z" fill="var(--navy)"/>
      <path d="M482,0 C452,130 382,200 302,245 C252,272 217,290 202,309" fill="none" stroke="var(--red)" stroke-width="4"/>
    </svg>

    <div class="brand">
      <div class="brand-name">Varko Works</div>
      <div class="brand-rule"></div>
    </div>

    <div class="contact">
      <p class="address">18761 52nd Avenue S<br>Kent, WA 98047</p>
      <ul class="contact-list">
        <li>
          <svg class="contact-icon" viewBox="0 0 24 24" aria-hidden="true"><path fill="var(--red)" d="M6.6 10.8a15.1 15.1 0 0 0 6.6 6.6l2.2-2.2a1 1 0 0 1 1-.25 11.4 11.4 0 0 0 3.6.57 1 1 0 0 1 1 1V20a1 1 0 0 1-1 1A17 17 0 0 1 3 4a1 1 0 0 1 1-1h3.5a1 1 0 0 1 1 1c0 1.25.2 2.45.57 3.6a1 1 0 0 1-.25 1z"/></svg>
          <span>(253) 617-4930</span>
        </li>
        <li>
          <svg class="contact-icon" viewBox="0 0 24 24" aria-hidden="true"><rect x="2" y="5" width="20" height="14" rx="1.5" fill="var(--red)"/><path d="M3 6l9 7 9-7" fill="none" stroke="var(--white)" stroke-width="1.6"/></svg>
          <span>martin@plumlinegroup.com</span>
        </li>
        <li>
          <svg class="contact-icon" viewBox="0 0 24 24" aria-hidden="true"><circle cx="12" cy="12" r="10" fill="var(--red)"/><path d="M2 12h20M12 2c3 3 3 17 0 20M12 2c-3 3-3 17 0 20" fill="none" stroke="var(--white)" stroke-width="1.3"/></svg>
          <span>www.varkoworks.com</span>
        </li>
      </ul>
    </div>
  </section>

  <section class="card card-back" aria-label="Business card back">
    <div class="brand">
      <div class="brand-name">Varko Works</div>
      <div class="brand-rule"></div>
    </div>
  </section>

</body>
</html>
```